Stationery for use with Ninefold Ridge reports

I would like to get a stationery design that my firm -- Ninefold Ridge Advisory -- will use as a format for reports that we send our clients. I am specifically looking for a design for use on a piece of paper or letterhead -- not business cards or envelopes.

We are an Africa based US risk intelligence and strategy firm that works with multinational corporations operating in West Africa. Our initial thinking is that we would like a color scheme consistent with our existing logo -- however we are open to other color schemes.

Also, we would like to see at least two separate versions: one with our company name and logo, the other without name and logo.

We also would like font recommendations for the stationary design.

The final design should communicate discreet professionalism and a modern approach, but it should not overshadow the words and information printed on the stationery.

Target Market(s)

Multinational corporations that currently use our products.

Font styles to use
Serif
Sans Serif

Requirements
Must have
• Sense of discreet professionalism that will not overshadow the content we put onto the stationery format.
• We would like to see designs with and without our company name/logo.
• Please suggest fonts that would work with the stationery.
Nice to have
• Ideally colors consistent with out existing logo, though we are open to and even encourage other ideas.
Should not have
• No need for business cards or envelopes.

```html
<!DOCTYPE html>
<html lang="en">
<head>
<meta charset="utf-8">
<title>Ninefold Ridge Advisory — Letterhead</title>
<link rel="stylesheet" href="https://fonts.googleapis.com/css2?family=Open+Sans:wght@400&display=swap">
<style>
  :root {
    --backdrop: #e4e4e4;
    --paper: #ffffff;
    --ink: #5f6266;
    --ink-dark: #24333f;
    --rule: #2a3640;
    --band-amber: #e0a64a;
    --band-sky: #a9d2ea;
    --signature-tone: #ececee;
  }
  * { margin: 0; padding: 0; box-sizing: border-box; }
  html, body {
    width: 1200px;
    height: 960px;
    overflow: hidden;
    background: var(--backdrop);
    font-family: "Open Sans", sans-serif;
  }
  .sheet {
    position: absolute;
    left: 298px;
    top: 47px;
    width: 598px;
    height: 852px;
    background: var(--paper);
    overflow: hidden;
  }
  .brand {
    position: absolute;
    left: 31px;
    top: 78px;
    display: flex;
    align-items: center;
    gap: 8px;
  }
  .brand-square {
    width: 12px;
    height: 12px;
    background: var(--ink-dark);
  }
  .brand-name {
    font-size: 15px;
    line-height: 20px;
    color: var(--ink-dark);
  }
  .header-rule {
    position: absolute;
    left: 31px;
    top: 108px;
    width: 536px;
    height: 2px;
    background: var(--rule);
  }
  .line {
    position: absolute;
    left: 59px;
    width: 500px;
    font-size: 9.8px;
    line-height: 14px;
    color: var(--ink);
    white-space: nowrap;
  }
  .signature {
    position: absolute;
    left: 417px;
    top: 593px;
    width: 120px;
    height: 39px;
    background: linear-gradient(90deg, var(--paper), var(--signature-tone) 40%, var(--paper));
  }
  .signatory {
    position: absolute;
    left: 421px;
    font-size: 9.8px;
    line-height: 13px;
    color: var(--ink);
  }
  .footer-band {
    position: absolute;
    left: 0;
    bottom: 0;
    width: 598px;
    height: 16px;
  }
</style>
</head>
<body>
  <main class="sheet">
    <div class="brand">
      <span class="brand-square"></span>
      <span class="brand-name">Ninefold Ridge Advisory</span>
    </div>
    <div class="header-rule"></div>

    <p class="line" style="top:255px">Date, 10 September, 2020</p>

    <p class="line" style="top:305px">This is a sample letter that has been placed to demonstrate typing remat (Your Company). letterhead</p>
    <p class="line" style="top:328px">design. When positioned properly, it will serve to work in harmony with all other elements letterhead.</p>
    <p class="line" style="top:350px">This letterhead design is meant to project an image</p>

    <p class="line" style="top:374px">This letterhead design is meant project an image of professionalism reliability. By using simple aligen</p>
    <p class="line" style="top:397px">we have created a very spacious feeling. The simplicity suggest&nbsp; rengththe spaciousnes contributes h</p>
    <p class="line" style="top:418px">aesthetics the layout. These basic qualities along with the (Your Company)</p>

    <p class="line" style="top:445px">look and helps reinforce the (Your Company) brand. letterhead design is meant to project an image p</p>
    <p class="line" style="top:467px">design. When positioned properly, it will serve to work in harmony all the other elements letterhead.</p>
    <p class="line" style="top:489px">sionalism and reliability.</p>

    <p class="line" style="top:518px">This letterhead design is based on the (Form of your logo) form (Your Company) logo. Each stationery</p>
    <p class="line" style="top:542px">we have created a very spacious feeling. The simplicity suggests strength the spaciousnes contribute</p>
    <p class="line" style="top:563px">part of the (Form of your logo).</p>

    <div class="signature" role="img" aria-label="Handwritten signature of Martin Ashby"></div>
    <p class="signatory" style="top:630px">Martin Ashby</p>
    <p class="signatory" style="top:642px">Manager</p>

    <svg class="footer-band" viewBox="0 0 598 16" aria-hidden="true">
      <polygon points="0,0 491,0 482,16 0,16" fill="var(--band-amber)"/>
      <polygon points="498,0 598,0 598,16 490,16" fill="var(--band-sky)"/>
    </svg>
  </main>
</body>
</html>
```